The Vantor Codex Book Cover

"The Vantor Codex" is a book I wrote with the slogan "Unlock Performance, Spark Engagement: Master the Art of Building Winning Cultures in Today's Hybrid World". The book is designed around a methodology that's mine and that I attached. I would love to see the graphic of the methodology integrated in the design in a very subtle way. Use colors from the model but the book cover should be catchy, modern and engaging to the eye.
Overall the book is about three key elements towards success:
- (Self) Directions (purpose)
- Human experience (people and psychological safety)
- Maximize engagement
The methodology is a FLOW so flow is something that could be incorporated as well in the concept.
Low design quality
Managers and Teams

```html
<!DOCTYPE html>
<html lang="en">
<head>
<meta charset="utf-8">
<title>The Vantor Codex – Book Cover Options</title>
<link href="https://fonts.googleapis.com/css2?family=Bebas+Neue&family=Oswald:wght@200;700&family=Playfair+Display:ital,wght@0,800;1,900&display=swap" rel="stylesheet">
<style>
  :root {
    --stage: #dadada;
    --paper: #ffffff;
    --ink: #111111;
    --title-top: #0c5b95;
    --title-bottom: #1ba3de;
    --flow-pink: #e9587a;
    --flow-magenta: #b14f8c;
    --flow-purple: #5a3f7f;
    --flow-blue: #3e7fbf;
    --flow-teal: #8fd0d6;
    --flow-lime: #d2d45e;
    --flow-gold: #f0c64a;
  }
  * { margin: 0; padding: 0; box-sizing: border-box; }
  html, body { width: 1200px; height: 848px; overflow: hidden; background: var(--stage); }
  .stage { position: relative; width: 1200px; height: 848px; }

  .cover {
    position: absolute;
    top: 80px;
    width: 535px;
    height: 686px;
    background: var(--paper);
    overflow: hidden;
  }
  .cover--compact { left: 43px; }
  .cover--bold { left: 625px; }

  .tagline {
    position: absolute;
    height: 22px;
    border-top: 2px solid var(--ink);
    border-bottom: 1px solid var(--ink);
    font-family: "Oswald", sans-serif;
    font-weight: 700;
    font-size: 9px;
    letter-spacing: 2.6px;
    color: var(--ink);
    text-align: center;
    line-height: 19px;
    white-space: nowrap;
    z-index: 1;
  }

  .title-the, .title-word {
    position: absolute;
    left: 0;
    width: 100%;
    text-align: center;
    font-family: "Playfair Display", serif;
    line-height: 1;
    white-space: nowrap;
  }
  .title-the {
    font-style: italic;
    font-weight: 900;
    color: var(--ink);
    letter-spacing: -2px;
    z-index: 2;
  }
  .title-word {
    font-weight: 800;
    letter-spacing: -3px;
    background: linear-gradient(180deg, var(--title-top) 20%, var(--title-bottom) 85%);
    -webkit-background-clip: text;
    background-clip: text;
    color: transparent;
  }

  .subtitle {
    position: absolute;
    left: 0;
    width: 100%;
    text-align: center;
    font-family: "Bebas Neue", sans-serif;
    color: var(--ink);
  }

  .flow-artwork {
    position: absolute;
    border-radius: 50% / 50%;
    background:
      linear-gradient(120deg, var(--flow-pink) 0%, var(--flow-magenta) 20%, var(--flow-purple) 35%, var(--flow-blue) 50%, var(--flow-teal) 70%, var(--flow-lime) 88%, var(--flow-gold) 100%);
    opacity: 0.85;
  }

  .author {
    position: absolute;
    left: 0;
    width: 100%;
    top: 624px;
    text-align: center;
    font-family: "Oswald", sans-serif;
    font-size: 37px;
    line-height: 44px;
    letter-spacing: 0.55em;
    color: var(--ink);
    white-space: nowrap;
  }
  .author-first { font-weight: 200; margin-right: 0.4em; }
  .author-last { font-weight: 700; }

  /* compact variant */
  .cover--compact .tagline--left { left: 53px; top: 48px; width: 154px; }
  .cover--compact .tagline--right { left: 309px; top: 48px; width: 152px; }
  .cover--compact .title-the { top: 34px; font-size: 52px; }
  .cover--compact .title-word--first { top: 68px; font-size: 96px; }
  .cover--compact .title-word--second { top: 129px; font-size: 113px; }
  .cover--compact .subtitle { top: 262px; font-size: 27px; line-height: 34px; }
  .cover--compact .flow-artwork { left: 65px; top: 330px; width: 404px; height: 268px; }

  /* bold variant */
  .cover--bold .tagline--left { left: 45px; top: 44px; width: 164px; }
  .cover--bold .tagline--right { left: 323px; top: 44px; width: 164px; }
  .cover--bold .title-the { top: 24px; font-size: 62px; }
  .cover--bold .title-word--first { top: 65px; font-size: 113px; }
  .cover--bold .title-word--second { top: 155px; font-size: 119px; }
  .cover--bold .subtitle { top: 309px; font-size: 32px; line-height: 42px; }
  .cover--bold .flow-artwork { left: 119px; top: 398px; width: 304px; height: 208px; }
</style>
</head>
<body>
<main class="stage">

  <article class="cover cover--compact">
    <div class="tagline tagline--left">UNLOCK PERFORMANCE</div>
    <div class="tagline tagline--right">SPARK ENGAGEMENT</div>
    <h1 class="title">
      <span class="title-the">The</span>
      <span class="title-word title-word--first">Vantor</span>
      <span class="title-word title-word--second">Codex</span>
    </h1>
    <p class="subtitle">10 steps to unleash your<br>team's full potential</p>
    <div class="flow-artwork" role="img" aria-label="Flow methodology artwork: colourful segmented ring with a compass, globe and team figures"></div>
    <p class="author"><span class="author-first">DAAN</span><span class="author-last">VERHOEK</span></p>
  </article>

  <article class="cover cover--bold">
    <div class="tagline tagline--left">UNLOCK PERFORMANCE</div>
    <div class="tagline tagline--right">SPARK ENGAGEMENT</div>
    <h1 class="title">
      <span class="title-the">The</span>
      <span class="title-word title-word--first">Vantor</span>
      <span class="title-word title-word--second">Codex</span>
    </h1>
    <p class="subtitle">10 steps to unleash your<br>team's full potential</p>
    <div class="flow-artwork" role="img" aria-label="Flow methodology artwork: colourful segmented ring with a compass, globe and team figures"></div>
    <p class="author"><span class="author-first">DAAN</span><span class="author-last">VERHOEK</span></p>
  </article>

</main>
</body>
</html>
```